Corvanth Veylor - Advanced Skincare and undetectable Makeup for Men

We are in need of a professional webpage for our company Corvanth Veylor. We help every man feel his best by looking his best. Inspired by the myth of Corvanth, we offer makeup and skincare products along with education upon their use. Our mission is to celebrate masculinity in all of its forms, regardless of age, race, sexual orientation, or assigned gender at birth.

The webpage would serve as our online store, as a place where our clients can learn about our brand, view our "How-to" video tutorials, and get product information. An online blog will also be hosted in order to keep clients up to date with news, updates, media mentions, etc.

The color schemes that we use are mostly Black and Gold, with Red accents. please keep in mind that this is a men's cosmetics line, and therefore should read powerful, sexy, confident and bold - all with a high end look and feel.

Think along the lines of brands like Lem Brisko, QDV, Belluti, etc.

our logo is included in the files attached. images and copy will be added in at a later time; hence, general images that fit the feel and filler text is encouraged.

The products to be sold include:
a face cleanser in a pump dispenser bottle (1 size)
a mask in a round jar container (1 size)
a moisturizer in a pump container 1 size)
a concealer in a click pen with a brush applicator (3 shades)
a liquid liner pen (4 shades)
a contouring palette (2 shade options)
a setting spray (single option)

Target Market(s)

Millennial Men

Industry/Entity Type

Beauty

Number of Pages Required

5+ page

Font styles to use
Serif

Colors
ec1f27
000000
faa54b

Requirements
Must have
• ur essential requirements are:
• 1) a stunning and engaging landing page that truly captures the ideals of sexuality, boldness and confidence.
• 2) an interactive and engaging online store that is easy to update / add product / information to.
• 3) Product pages supporting various toggling images of the product, a shade selection option, ingredient information, usage instructions, pricing, and a link to a "how to video" unique to each individual product.
• 4) dedicated space where all of the tutorials can be organized together
• 5) an organized Blog section, that would include a segment for a Q&A section for us to update as the brand grows, ongoing contests (that would be easily hidden if there are no contests running at the moment) as well as general news and updates segment.
• 6) an "about us" page, where our customers are able to learn about our story, inspirations, humanitarian efforts and philosophies in product contents and purity.
• 7) a contact us page, which would include social media links, contact email and telephone number as well as physical address to be updated upon launch.
• 8) discrete privacy policy, terms of use, and return policy links available at the bottom of every page
Nice to have
• 1) A posting forum where clients could post their looks using our products, or maybe a live stream of our Pictoval account.
• 2) a member sign in page so that we can collect and store customer information for faster check out, keep track of purchases attached to their email address (future loyalty program plans) and maintain an email database for email notifications and the such.

```html
<!DOCTYPE html>
<html lang="en">
<head>
<meta charset="utf-8">
<title>Corvanth Veylor</title>
<link href="https://fonts.googleapis.com/css2?family=Open+Sans:wght@300;400;600;700&family=Cinzel:wght@500&display=swap" rel="stylesheet">
<style>
:root{
  --gold:#f5ab0f;
  --gold-btn:#fbb216;
  --red:#ea1a2b;
  --black:#141414;
  --band-1:#1f1f1f;
  --band-2:#262626;
  --band-3:#1b1b1b;
  --text:#9a9a9a;
  --white:#ffffff;
  --btn-dark:#454545;
  --brand-brown:#9b6a2c;
}
*{box-sizing:border-box;margin:0;padding:0}
html,body{width:1200px;height:2922px;overflow:hidden;background:var(--black)}
body{font-family:"Open Sans",Arial,sans-serif;color:var(--text);position:relative}
h1,h2,h3,h4{font-weight:400}
.section{position:absolute;left:0;width:1200px}
.section-title{position:absolute;left:0;width:1200px;text-align:center;color:var(--gold);font-size:33px;font-weight:400;letter-spacing:.5px;line-height:40px}

/* hero */
.hero{top:0;height:616px;background:
  radial-gradient(ellipse 260px 330px at 800px 330px,rgba(168,88,40,.95),rgba(168,88,40,0) 75%),
  radial-gradient(ellipse 190px 230px at 930px 250px,rgba(214,170,140,.85),rgba(214,170,140,0) 75%),
  radial-gradient(ellipse 220px 300px at 1010px 420px,rgba(200,150,120,.7),rgba(200,150,120,0) 75%),
  linear-gradient(90deg,#4c4a49 0%,#5d5a58 45%,#5a4c44 100%)}
.nav{position:absolute;top:0;left:0;width:1200px;height:38px;background:rgba(20,20,20,.55)}
.nav a{position:absolute;top:11px;font-size:12px;color:#bdbdbd;text-decoration:none;letter-spacing:.3px;white-space:nowrap}
.nav a.active{color:var(--white)}
.nav svg{position:absolute;top:10px}
.logo-box{position:absolute;left:132px;top:0;width:308px;height:168px;background:var(--white)}
.logo-box span{position:absolute;left:0;bottom:16px;width:100%;text-align:center;white-space:nowrap;font-family:"Cinzel",Georgia,serif;font-weight:500;color:var(--brand-brown);font-size:20px;letter-spacing:3px}
.hero-title{position:absolute;left:132px;top:248px;color:var(--white);font-size:38px;font-weight:400;line-height:48px;letter-spacing:.3px;white-space:nowrap}
.btn-shop{position:absolute;left:132px;top:351px;width:141px;height:45px;background:var(--gold-btn);color:#1a1a1a;font-size:17px;font-weight:600;display:flex;align-items:center;justify-content:center}
.arrow{position:absolute}

/* about */
.about{top:616px;height:358px;background:var(--band-1)}
.about .section-title{top:66px}
.about-mark{position:absolute;top:158px;left:0;width:1200px;text-align:center;font-family:"Cinzel",Georgia,serif;color:#b8b8b8;font-size:9px;letter-spacing:3px}
.about-text{position:absolute;left:132px;top:177px;width:936px;text-align:center;font-size:13px;line-height:25.5px;color:#8e8e8e}

/* products */
.products{top:974px;height:512px;background:var(--band-2)}
.products .section-title{top:70px}
.card{position:absolute;top:134px;width:220px;height:297px;border:1px solid #9b9b9b}
.card-img{position:absolute;left:7px;top:7px;width:204px;height:179px;background:#fff}
.card-name{position:absolute;top:201px;width:100%;text-align:center;font-size:13px;color:#9d9d9d}
.card-price{position:absolute;top:224px;width:100%;text-align:center;font-size:13px;color:#9d9d9d}
.card-btn{position:absolute;top:255px;width:101px;height:37px;background:var(--btn-dark);color:#e6e6e6;font-size:13px;display:flex;align-items:center;justify-content:center;gap:5px}

/* video */
.video{top:1486px;height:462px;background:
  radial-gradient(ellipse 150px 200px at 420px 230px,rgba(196,150,130,.85),rgba(196,150,130,0) 80%),
  radial-gradient(ellipse 130px 260px at 300px 300px,rgba(40,28,24,.8),rgba(40,28,24,0) 80%),
  linear-gradient(90deg,#6a5853 0%,#7b655f 35%,#6f5b57 60%,#6d5a56 100%)}
.play{position:absolute;left:569px;top:199px}

/* blog */
.blog{top:1948px;height:507px;background:var(--band-3)}
.blog .section-title{top:64px}
.post{position:absolute;top:127px;width:445px;height:230px;background:#ebebeb}
.post-img{position:absolute;left:0;top:0;width:193px;height:230px}
.post-body{position:absolute;left:220px;top:18px;width:205px}
.post-title{font-size:15px;line-height:20px;color:#222}
.post-text{margin-top:12px;font-size:10px;line-height:16.5px;color:#444}
.btn-read{display:inline-block;margin-top:18px;width:87px;height:29px;border:1px solid #8a8a8a;font-size:10px;color:#666;text-align:center;line-height:27px}
.btn-all{position:absolute;left:557px;top:390px;width:86px;height:39px;border:1px solid #bdbdbd;color:#a8a8a8;font-size:10px;text-align:center;line-height:37px}

/* newsletter */
.newsletter{top:2455px;height:132px;background:var(--band-2)}
.newsletter-title{position:absolute;left:224px;top:48px;color:var(--gold);font-size:33px;font-weight:400;letter-spacing:.3px;line-height:40px;white-space:nowrap}
.email{position:absolute;left:643px;top:50px;width:232px;height:37px;background:#cfcfcf;color:#333;font-size:11px;padding-left:16px;line-height:37px}
.btn-sub{position:absolute;left:875px;top:50px;width:97px;height:37px;background:var(--red);color:var(--white);font-size:12px;font-weight:700;text-align:center;line-height:37px}

/* footer */
.footer{top:2587px;height:335px;background:var(--band-3)}
.foot-col{position:absolute;top:58px}
.foot-col h4{color:var(--gold);font-size:13px;font-weight:600;margin-bottom:18px;letter-spacing:.3px}
.foot-col ul{list-style:none;font-size:11px;line-height:20.5px;color:#8a8a8a}
.foot-links{display:flex;gap:25px}
.social,.pay{display:flex;gap:14px;margin-top:2px}
.social i{width:13px;height:13px;border-radius:50%;background:#a9a9a9;display:block}
.pay{gap:8px}
.pay i{width:23px;height:14px;border-radius:2px;background:#a9a9a9;display:block}
.divider{position:absolute;left:132px;top:218px;width:936px;height:1px;background:#333}
.copyright{position:absolute;top:260px;width:1200px;text-align:center;font-size:11px;color:#6e6e6e}
</style>
</head>
<body>

<header class="section hero" role="img" aria-label="Photo of a model with long copper-red wavy hair">
  <nav class="nav">
    <a class="active" style="left:607px">HOME</a>
    <a style="left:669px">PRODUCTS</a>
    <a style="left:760px">VIDEOS</a>
    <a style="left:831px">BLOG</a>
    <a style="left:889px">LOGIN / REGISTER</a>
    <svg style="left:1010px" width="17" height="17" viewBox="0 0 17 17"><circle cx="7" cy="7" r="5" fill="none" stroke="#d0d0d0" stroke-width="2"/><line x1="10.5" y1="10.5" x2="15" y2="15" stroke="#d0d0d0" stroke-width="2"/></svg>
    <svg style="left:1048px" width="18" height="17" viewBox="0 0 18 17"><path d="M1 6h16l-2 9H3z" fill="none" stroke="#d0d0d0" stroke-width="1.8"/><path d="M5 6l4-5 4 5" fill="none" stroke="#d0d0d0" stroke-width="1.6"/></svg>
  </nav>
  <div class="logo-box"><span>CORVANTH VEYLOR</span></div>
  <h1 class="hero-title">MAECENAS VEL<br>TORTOR ACCUMSAN</h1>
  <div class="btn-shop">SHOP NOW</div>
  <svg class="arrow" style="left:56px;top:312px" width="16" height="28" viewBox="0 0 16 28"><path d="M14 2L3 14l11 12" fill="none" stroke="#cfcfcf" stroke-width="3"/></svg>
  <svg class="arrow" style="left:1127px;top:312px" width="16" height="28" viewBox="0 0 16 28"><path d="M2 2l11 12L2 26" fill="none" stroke="#cfcfcf" stroke-width="3"/></svg>
</header>

<section class="section about">
  <h2 class="section-title">ABOUT OUR BRAND</h2>
  <div class="about-mark">CORVANTH VEYLOR</div>
  <p class="about-text">Nulla tristique posuere molestie. Aliquam erat volutpat. Etiam quis aliquet risus. Duis ornare erat eget magna dapibus, in accumsan quam pharetra. Nam tempus, quam in bibendum vulputate, sapien dolor viverra nisl, vitae euismod elit turpis et nulla. Aliquam erat volutpat. Pellentesque blandit lacus eget nunc faucibus, et tincidunt eros viverra. Phasellus consequat sagittis nisi suscipit feugiat. Cras eget leo sed nunc hendrerit ultricies eu at nisl. Praesent iaculis faucibus urna sit amet lacinia. Maecenas consequat justo enim, ac mattis massa imperdiet quis.</p>
</section>

<section class="section products">
  <h2 class="section-title">OUR PRODUCTS</h2>
  <svg class="arrow" style="left:56px;top:248px" width="16" height="28" viewBox="0 0 16 28"><path d="M14 2L3 14l11 12" fill="none" stroke="#bdbdbd" stroke-width="3"/></svg>
  <svg class="arrow" style="left:1127px;top:248px" width="16" height="28" viewBox="0 0 16 28"><path d="M2 2l11 12L2 26" fill="none" stroke="#bdbdbd" stroke-width="3"/></svg>

  <div class="card" style="left:132px">
    <div class="card-img" role="img" aria-label="Product photo: pink face cleanser pump bottle" style="background:radial-gradient(ellipse 30px 70px at 102px 95px,#f2c4dc,#ffffff 90%)"></div>
    <div class="card-name">Face Cleanser</div><div class="card-price">$28.00</div>
    <div class="card-btn" style="left:7px"><svg width="11" height="11"><circle cx="5.5" cy="5.5" r="5.5" fill="#eee"/><path d="M4 3l4 2.5L4 8z" fill="#454545"/></svg>How-To</div>
    <div class="card-btn" style="left:111px"><svg width="13" height="9"><ellipse cx="6.5" cy="4.5" rx="6" ry="4" fill="#eee"/><circle cx="6.5" cy="4.5" r="2" fill="#454545"/></svg>View Info</div>
  </div>
  <div class="card" style="left:372px">
    <div class="card-img" role="img" aria-label="Product photo: round cream mask jar" style="background:radial-gradient(ellipse 80px 55px at 102px 95px,#dcd0cc,#ffffff 90%)"></div>
    <div class="card-name">Mask</div><div class="card-price">$23.00</div>
    <div class="card-btn" style="left:7px"><svg width="11" height="11"><circle cx="5.5" cy="5.5" r="5.5" fill="#eee"/><path d="M4 3l4 2.5L4 8z" fill="#454545"/></svg>How-To</div>
    <div class="card-btn" style="left:111px"><svg width="13" height="9"><ellipse cx="6.5" cy="4.5" rx="6" ry="4" fill="#eee"/><circle cx="6.5" cy="4.5" r="2" fill="#454545"/></svg>View Info</div>
  </div>
  <div class="card" style="left:610px">
    <div class="card-img" role="img" aria-label="Product photo: clear moisturizer pump bottle" style="background:radial-gradient(ellipse 25px 70px at 102px 95px,#dfe2e4,#ffffff 90%)"></div>
    <div class="card-name">Moisturizer</div><div class="card-price">$36.00</div>
    <div class="card-btn" style="left:7px"><svg width="11" height="11"><circle cx="5.5" cy="5.5" r="5.5" fill="#eee"/><path d="M4 3l4 2.5L4 8z" fill="#454545"/></svg>How-To</div>
    <div class="card-btn" style="left:111px"><svg width="13" height="9"><ellipse cx="6.5" cy="4.5" rx="6" ry="4" fill="#eee"/><circle cx="6.5" cy="4.5" r="2" fill="#454545"/></svg>View Info</div>
  </div>
  <div class="card" style="left:848px">
    <div class="card-img" role="img" aria-label="Product photo: row of concealer pens" style="background:radial-gradient(ellipse 70px 70px at 102px 95px,#c9ccce,#ffffff 90%)"></div>
    <div class="card-name">Concealer</div><div class="card-price">$16.00</div>
    <div class="card-btn" style="left:7px"><svg width="11" height="11"><circle cx="5.5" cy="5.5" r="5.5" fill="#eee"/><path d="M4 3l4 2.5L4 8z" fill="#454545"/></svg>How-To</div>
    <div class="card-btn" style="left:111px"><svg width="13" height="9"><ellipse cx="6.5" cy="4.5" rx="6" ry="4" fill="#eee"/><circle cx="6.5" cy="4.5" r="2" fill="#454545"/></svg>View Info</div>
  </div>
</section>

<section class="section video" role="img" aria-label="Video still of a model touching her face, tutorial video">
  <svg class="play" width="62" height="62" viewBox="0 0 62 62"><circle cx="31" cy="31" r="31" fill="#ffffff"/><path d="M24 18l21 13-21 13z" fill="#111"/></svg>
</section>

<section class="section blog">
  <h2 class="section-title">BLOG</h2>
  <article class="post" style="left:132px">
    <div class="post-img" role="img" aria-label="Close-up photo of flowing brown hair" style="background:linear-gradient(135deg,#3a2315,#9a5a2c 45%,#5a3520 70%,#2c1a10)"></div>
    <div class="post-body">
      <h3 class="post-title">Etiam mattis augue vehicula odio posuere, sit amet</h3>
      <p class="post-text">Etiam mattis augue vehicula odio posuere, sit amet tempus lectus luctus. Nulla facilisi. Etiam vel massa elementum, bibendum tellus venenatis, feugiat massa.</p>
      <span class="btn-read">Read More</span>
    </div>
  </article>
  <article class="post" style="left:623px">
    <div class="post-img" role="img" aria-label="Flat-lay photo of makeup products and brushes" style="background:linear-gradient(135deg,#f2efec,#d9cfc6 50%,#efe9e4)"></div>
    <div class="post-body">
      <h3 class="post-title">Curabitur venenatis lacinia ornare. Cras sollicitudin</h3>
      <p class="post-text">Etiam mattis augue vehicula odio posuere, sit amet tempus lectus luctus. Nulla facilisi. Etiam vel massa elementum, bibendum tellus venenatis, feugiat massa.</p>
      <span class="btn-read">Read More</span>
    </div>
  </article>
  <div class="btn-all">View All</div>
</section>

<section class="section newsletter">
  <h2 class="newsletter-title">NEWSLETTER SUBSCRIBE</h2>
  <div class="email">Email Address</div>
  <div class="btn-sub">SUBSCRIBE</div>
</section>

<footer class="section footer">
  <div class="foot-col" style="left:132px">
    <h4>LINKS</h4>
    <div class="foot-links">
      <ul><li>Home</li><li>Products</li><li>Videos</li><li>Blog</li></ul>
      <ul><li>Login</li><li>Register</li></ul>
    </div>
  </div>
  <div class="foot-col" style="left:382px">
    <h4>MY ACCOUNT</h4>
    <ul><li>My Cart</li><li>My Wishlist</li><li>Checkout</li><li>Shipping &amp; Returns</li></ul>
  </div>
  <div class="foot-col" style="left:629px">
    <h4>FOLLOW US ON</h4>
    <div class="social" aria-label="Social links"><i></i><i></i><i></i><i></i></div>
  </div>
  <div class="foot-col" style="left:916px">
    <h4>PAYMENTS</h4>
    <div class="pay" aria-label="Accepted payment cards"><i></i><i></i><i></i><i></i><i></i></div>
  </div>
  <div class="divider"></div>
  <div class="copyright">Copyright &copy; 2018 Corvanth Veylor. All rights reserved</div>
</footer>

</body>
</html>
```